Thornvale Group needs a business card design

We need a new business card design using the logo recently selected in a logo competition on Pixel Bazaar. Our business is a consultancy specializing in aviation and energy and the winning business card design will promote an image of precision and professionalism with creativity.

Please use the logo with the name on the front of the card and use a complementary font. Make the back white with either the light grey or dark grey logo.

Target Market(s)

Senior finance and legal leaders at aviation and energy companies

Industry/Entity Type

Management Consulting

Contact Information for Business Card

Peter Castrell
President
Thornvale Group

www.thornvalegroup.example

(555) 204-6391
pc@thornvalegroup.example

Requirements
Must have
• Professional font that goes well with the logo font

```html
<!DOCTYPE html>
<html lang="en">
<head>
<meta charset="utf-8">
<title>Thornvale Group – Business Card</title>
<link rel="stylesheet" href="https://fonts.googleapis.com/css2?family=Arimo:wght@400;700&display=swap">
<style>
  :root {
    --navy: #0f3566;
    --navy-deep: #0a2748;
    --navy-light: #1c4a80;
    --stripe: #7b7f86;
    --paper: #ffffff;
    --ink: #3c3f44;
    --backdrop: #e9eaec;
    --on-navy: #e8ecf2;
  }
  * { box-sizing: border-box; margin: 0; padding: 0; }
  html, body {
    width: 1200px;
    height: 950px;
    overflow: hidden;
    background: var(--backdrop);
    font-family: "Arimo", Arial, sans-serif;
  }
  .stage {
    position: relative;
    width: 1200px;
    height: 950px;
  }
  .card {
    position: absolute;
    left: 260px;
    width: 680px;
    height: 388px;
    overflow: hidden;
    box-shadow: 0 6px 18px rgba(0,0,0,0.18);
  }
  .card--front { top: 60px; background: var(--paper); }
  .card--back {
    top: 502px;
    background: linear-gradient(135deg, var(--navy-light) 0%, var(--navy) 50%, var(--navy-deep) 100%);
  }

  .front-shapes { position: absolute; inset: 0; }

  .brand-name {
    position: absolute;
    left: 44px;
    top: 44px;
    color: var(--navy);
    font-weight: 400;
    font-size: 30px;
    letter-spacing: 0.14em;
    line-height: 1;
  }

  .company-details {
    position: absolute;
    left: 44px;
    top: 104px;
    color: var(--ink);
    font-size: 16px;
    line-height: 1.32;
  }

  .contact-list {
    position: absolute;
    left: 44px;
    top: 184px;
    list-style: none;
    color: var(--ink);
    font-size: 16px;
    line-height: 1.55;
  }
  .contact-list li { display: flex; align-items: center; gap: 10px; }
  .contact-list svg { width: 14px; height: 14px; fill: var(--navy); flex: none; }

  .person {
    position: absolute;
    right: 44px;
    bottom: 42px;
    text-align: right;
    color: var(--on-navy);
  }
  .person__name { font-weight: 700; font-size: 22px; letter-spacing: 0.03em; }
  .person__title { font-size: 18px; margin-top: 6px; }

  .back-brand {
    position: absolute;
    left: 0; right: 0;
    top: 150px;
    text-align: center;
    color: #c9ced6;
    font-size: 38px;
    font-weight: 400;
    letter-spacing: 0.14em;
  }
  .back-url {
    position: absolute;
    left: 0; right: 0;
    bottom: 70px;
    text-align: center;
    color: #9fb0c6;
    font-size: 16px;
    letter-spacing: 0.08em;
  }
</style>
</head>
<body>
<main class="stage">

  <section class="card card--front" aria-label="Business card front">
    <svg class="front-shapes" viewBox="0 0 680 388" preserveAspectRatio="none" aria-hidden="true">
      <defs>
        <linearGradient id="panelFill" x1="0" y1="0" x2="1" y2="1">
          <stop offset="0" stop-color="#1c4a80"/>
          <stop offset="0.6" stop-color="#0f3566"/>
          <stop offset="1" stop-color="#0a2748"/>
        </linearGradient>
      </defs>
      <polygon points="268,388 680,116 680,128 292,388" fill="#7b7f86"/>
      <polygon points="302,388 680,136 680,388" fill="url(#panelFill)"/>
    </svg>

    <div class="brand-name">THORNVALE GROUP</div>

    <p class="company-details">
      Thornvale Group LLC<br>
      Finance and Strategy Consulting<br>
      Aviation - Manufacturing - Energy
    </p>

    <ul class="contact-list">
      <li>
        <svg viewBox="0 0 24 24" aria-hidden="true"><path d="M6.6 10.8a15.1 15.1 0 0 0 6.6 6.6l2.2-2.2a1 1 0 0 1 1-.25 11.4 11.4 0 0 0 3.6.57 1 1 0 0 1 1 1V20a1 1 0 0 1-1 1A17 17 0 0 1 3 4a1 1 0 0 1 1-1h3.5a1 1 0 0 1 1 1c0 1.25.2 2.45.57 3.57a1 1 0 0 1-.25 1z"/></svg>
        (555) 204-6391
      </li>
      <li>
        <svg viewBox="0 0 24 24" aria-hidden="true"><path d="M2 5h20v14H2z M2 5l10 8 10-8" fill="none" stroke="#0f3566" stroke-width="2.4"/></svg>
        pc@thornvalegroup.example
      </li>
      <li>
        <svg viewBox="0 0 24 24" aria-hidden="true"><circle cx="12" cy="12" r="10"/><path d="M2 12h20M12 2c3 3 3 17 0 20M12 2c-3 3-3 17 0 20" fill="none" stroke="#fff" stroke-width="1.4"/></svg>
        thornvalegroup.example
      </li>
    </ul>

    <div class="person">
      <div class="person__name">Peter J. Castrell</div>
      <div class="person__title">President</div>
    </div>
  </section>

  <section class="card card--back" aria-label="Business card back">
    <div class="back-brand">THORNVALE GROUP</div>
    <div class="back-url">thornvalegroup.example</div>
  </section>

</main>
</body>
</html>
```